Floor Inspections and Consulting

We provide inspections and consulting services on various floor coverings, e.g. carpet, hardwood, etc. We also do expert witness work for attorneys due to floor covering failures. We current have a logo, just need it incorporated into a new design. I have examples of cards I have found on the internet that capture my attention and make a statement. I have included our original business card, which in my opinion is terrible, but it does have our logo on it.

```html
<!DOCTYPE html>
<html lang="en">
<head>
<meta charset="utf-8">
<title>Keystone Floor Inspections – Business Card</title>
<link href="https://fonts.googleapis.com/css2?family=Roboto:wght@400;700;900&display=swap" rel="stylesheet">
<style>
  :root {
    --stage: #1b1b1b;
    --wood-dark: #3a2416;
    --wood-mid: #6b4429;
    --wood-light: #8a5c38;
    --orange: #e8760f;
    --gold: #f0a01e;
    --charcoal: #444444;
    --ink: #1f1f1f;
    --paper: #ffffff;
    --rule: #bdbdbd;
  }
  * { box-sizing: border-box; margin: 0; padding: 0; }
  html, body { width: 1200px; height: 900px; overflow: hidden; }
  body {
    background: var(--stage);
    font-family: "Roboto", Arial, sans-serif;
    display: flex;
    flex-direction: column;
    align-items: center;
    justify-content: center;
    gap: 40px;
  }
  .card {
    width: 560px;
    height: 320px;
    position: relative;
    overflow: hidden;
    box-shadow: 0 10px 30px rgba(0,0,0,.6);
  }

  /* Front */
  .card-front { color: var(--paper); }
  .wood-texture {
    position: absolute; inset: 0;
    background: linear-gradient(160deg, var(--wood-light) 0%, var(--wood-mid) 45%, var(--wood-dark) 100%);
  }
  .front-brand {
    position: absolute; top: 90px; left: 0; right: 0;
    display: flex; align-items: center; justify-content: center; gap: 16px;
  }
  .front-brand .mark { width: 24px; height: 24px; background: var(--paper); flex: none; }
  .front-name {
    font-weight: 900; font-size: 36px; line-height: 1.1; letter-spacing: 1px;
    text-transform: uppercase; color: var(--paper);
    white-space: nowrap;
  }
  .front-tagline {
    position: absolute; bottom: 40px; left: 0; right: 0;
    text-align: center;
    font-weight: 700; font-size: 17px; color: var(--gold);
  }

  /* Back */
  .card-back { background: var(--paper); display: flex; align-items: center; }
  .brand {
    width: 290px; padding-left: 30px; padding-right: 16px;
    display: flex; flex-direction: column; gap: 8px;
  }
  .brand-name {
    display: flex; align-items: center; gap: 10px;
    font-weight: 900; font-size: 24px; line-height: 1.05;
    text-transform: uppercase; color: var(--orange);
    white-space: nowrap;
  }
  .brand-name .mark { width: 18px; height: 18px; background: var(--charcoal); flex: none; }
  .brand-sub {
    border-bottom: 1.5px solid var(--orange);
    font-weight: 700; font-size: 10px; letter-spacing: 1px;
    color: var(--orange); text-transform: uppercase;
    padding-bottom: 4px; padding-left: 28px;
  }
  .divider { width: 1px; height: 130px; background: var(--rule); flex: none; }
  .contact { padding-left: 26px; }
  .contact-name {
    font-weight: 900; font-size: 22px; color: var(--orange);
    text-transform: uppercase; margin-bottom: 16px; letter-spacing: .5px;
  }
  .contact-list { list-style: none; display: flex; flex-direction: column; gap: 6px; }
  .contact-list li {
    display: flex; align-items: center; gap: 6px;
    font-size: 16px; color: var(--ink); white-space: nowrap;
  }
  .contact-list svg { width: 16px; height: 16px; flex: none; }
</style>
</head>
<body>

<section class="card card-front">
  <div class="wood-texture" role="img" aria-label="Weathered dark wooden floorboards running horizontally"></div>
  <div class="front-brand">
    <span class="mark"></span>
    <div class="front-name">Keystone Floor<br>Inspections</div>
  </div>
  <p class="front-tagline">Certified Floor Covering Inspection &amp; Consulting</p>
</section>

<section class="card card-back">
  <div class="brand">
    <div class="brand-name"><span class="mark"></span><span>Keystone Floor<br>Inspections</span></div>
    <div class="brand-sub">Analysis &amp; Consulting</div>
  </div>
  <div class="divider"></div>
  <div class="contact">
    <h1 class="contact-name">Dana Merrick</h1>
    <ul class="contact-list">
      <li>
        <svg viewBox="0 0 16 16" aria-hidden="true"><rect x="1" y="1" width="14" height="14" rx="2" fill="none" stroke="var(--orange)" stroke-width="1.5"/><path d="M5 4l2 2-1 1.3a6 6 0 0 0 2.7 2.7L10 9l2 2-1.3 1.3C7 12 4 9 3.7 5.3z" fill="var(--orange)"/></svg>
        555-214-7380
      </li>
      <li>
        <svg viewBox="0 0 16 16" aria-hidden="true"><rect x="1" y="3" width="14" height="10" fill="var(--orange)"/><path d="M1 3l7 6 7-6" fill="none" stroke="var(--paper)" stroke-width="1.2"/></svg>
        dana@keystonefloors.com
      </li>
      <li>
        <svg viewBox="0 0 16 16" aria-hidden="true"><circle cx="8" cy="8" r="7" fill="var(--orange)"/><g fill="none" stroke="var(--paper)" stroke-width="1"><ellipse cx="8" cy="8" rx="3" ry="7"/><path d="M1 8h14M2.5 4.5h11M2.5 11.5h11"/></g></svg>
        www.keystonefloors.com
      </li>
    </ul>
  </div>
</section>

</body>
</html>
```